Im open to ideas.. I was thinking on my business cards aswell as my logo. a place for my name. email. phone number and abn..

ive attched a file with my business logo. which i dont love the colours.. i was think a dark background with charcoal letters so something along those colour schumes but im open to ideas..

BRM Constructions

```html
<!DOCTYPE html>
<html lang="en">
<head>
<meta charset="utf-8">
<title>BRM Constructions – Business Cards</title>
<link rel="stylesheet" href="https://fonts.googleapis.com/css2?family=Open+Sans:wght@400;600;700&display=swap">
<style>
  :root {
    --backdrop: #3a2f2b;
    --card-front: #1f1f1f;
    --card-back: #050505;
    --ink-light: #d6d6d6;
    --ink-muted: #a9a9a9;
    --ink-soft: #8c8c8c;
  }
  * { margin: 0; padding: 0; box-sizing: border-box; }
  html, body {
    width: 1200px;
    height: 844px;
    overflow: hidden;
    background: var(--backdrop);
    font-family: "Open Sans", Arial, sans-serif;
  }
  .stage {
    position: relative;
    width: 1200px;
    height: 844px;
  }
  .card {
    position: absolute;
    width: 520px;
    height: 300px;
    border-radius: 3px;
    box-shadow: 0 14px 30px rgba(0,0,0,0.45);
  }
  .card--front {
    left: 60px;
    top: 330px;
    background: var(--card-front);
  }
  .card--back {
    left: 620px;
    top: 210px;
    background: var(--card-back);
  }

  /* Brand name lockup */
  .brand {
    position: absolute;
    display: flex;
    align-items: center;
    gap: 10px;
    color: var(--ink-light);
    font-weight: 700;
    letter-spacing: 1px;
    text-transform: uppercase;
    white-space: nowrap;
  }
  .brand__mark {
    background: var(--ink-light);
    flex: none;
  }
  .card--front .brand {
    right: 40px;
    top: 42px;
    font-size: 24px;
  }
  .card--front .brand__mark { width: 12px; height: 12px; }
  .card--back .brand {
    left: 50%;
    top: 50%;
    transform: translate(-50%, -50%);
    font-size: 38px;
  }
  .card--back .brand__mark { width: 18px; height: 18px; }

  /* Contact block */
  .contact {
    position: absolute;
    left: 38px;
    bottom: 34px;
    color: var(--ink-light);
  }
  .contact__name {
    font-size: 17px;
    font-weight: 600;
    line-height: 1.1;
  }
  .contact__role {
    font-size: 12.5px;
    color: var(--ink-muted);
    margin-bottom: 16px;
  }
  .contact__abn {
    font-size: 13px;
    font-weight: 700;
    margin-bottom: 14px;
  }
  .contact__list { list-style: none; }
  .contact__item {
    display: flex;
    align-items: center;
    gap: 10px;
    font-size: 13.5px;
    line-height: 22px;
  }
  .contact__icon {
    width: 11px;
    height: 11px;
    fill: var(--ink-soft);
    flex: none;
  }
</style>
</head>
<body>
<main class="stage">

  <section class="card card--front" aria-label="Business card front">
    <div class="brand">
      <span class="brand__mark"></span>
      <span class="brand__name">BRM Constructions</span>
    </div>

    <div class="contact">
      <p class="contact__name">Daniel Reeves</p>
      <p class="contact__role">Managing Director</p>
      <p class="contact__abn">ABN NO: 12345</p>
      <ul class="contact__list">
        <li class="contact__item">
          <svg class="contact__icon" viewBox="0 0 12 12" aria-hidden="true">
            <path d="M2.5 0.8 L4.3 0.8 L5 3.4 L3.8 4.4 C4.5 5.9 6 7.4 7.6 8.2 L8.6 7 L11.2 7.7 L11.2 9.5 C11.2 10.4 10.4 11.2 9.5 11.2 C4.9 11.2 0.8 7.1 0.8 2.5 C0.8 1.6 1.6 0.8 2.5 0.8 Z"/>
          </svg>
          <span>(044)-555-0192</span>
        </li>
        <li class="contact__item">
          <svg class="contact__icon" viewBox="0 0 12 12" aria-hidden="true">
            <path d="M0.5 2 H11.5 V10 H0.5 Z M1.3 2.6 L6 6.3 L10.7 2.6 Z" fill-rule="evenodd"/>
          </svg>
          <span>info@youremail.com</span>
        </li>
        <li class="contact__item">
          <svg class="contact__icon" viewBox="0 0 12 12" aria-hidden="true">
            <circle cx="6" cy="6" r="5.5"/>
            <path d="M0.8 6 H11.2 M6 0.6 C3.6 3.4 3.6 8.6 6 11.4 M6 0.6 C8.4 3.4 8.4 8.6 6 11.4" stroke="#1f1f1f" stroke-width="0.8" fill="none"/>
          </svg>
          <span>www.website.com</span>
        </li>
      </ul>
    </div>
  </section>

  <section class="card card--back" aria-label="Business card back">
    <div class="brand">
      <span class="brand__mark"></span>
      <span class="brand__name">BRM Constructions</span>
    </div>
  </section>

</main>
</body>
</html>
```